TorbCutters Website & website development in Wordpress

Simple website for a 5 pages with some 15 products for sale.
We will sell T shirts and other Viking mens grooming products.

*****Lady barbers****
Also the company that gets awarded this job needs to be able to give me a quote to build the site in wordpress, just a design will not work.

Target Market(s)

The adventurous person likes to travels and get a good haircut

Coding

Coded - Design and coding required

Number of Pages Required

5+ page

Font styles to use
Sans Serif

Colors
3176b5
33a6d7

Requirements
Must have
• Must have a product order page for T-Shirts
Must have a travel adventure page with up to 5 recommended adventures
Must have a link to our instagram @torbcuttersformen page that would allow a client to book a haircut
Should show female stylists cutting mens hair- So far the only pictures in the designs submitted are male barbers
Nice to have
• We have this set up in GoDaddy would like to use wordpress. Thanks!

```html
<!DOCTYPE html>
<html lang="en">
<head>
<meta charset="utf-8">
<title>TorbCutters – Livonia Barber Shop</title>
<link rel="stylesheet" href="https://fonts.googleapis.com/css2?family=Roboto+Condensed:wght@400;700&family=Raleway:wght@400;500&display=swap">
<style>
:root{
  --blue:#0b4c9b;
  --red:#e1262b;
  --ink:#333333;
  --muted:#555555;
  --white:#ffffff;
  --line:#8a8f96;
}
*{box-sizing:border-box;margin:0;padding:0}
html,body{width:1200px;height:4498px;overflow:hidden;background:var(--white)}
body{position:relative;font-family:"Roboto Condensed",sans-serif;color:var(--ink)}
.abs{position:absolute}

/* hero */
.hero{left:0;top:0;width:1200px;height:690px;
  background:
    radial-gradient(ellipse 420px 260px at 160px 150px,rgba(40,70,105,.85),rgba(40,70,105,0) 70%),
    radial-gradient(ellipse 380px 220px at 430px 330px,rgba(238,236,222,.9),rgba(238,236,222,0) 70%),
    radial-gradient(ellipse 300px 200px at 120px 520px,rgba(205,198,178,.8),rgba(205,198,178,0) 70%),
    radial-gradient(ellipse 360px 520px at 1000px 260px,rgba(120,58,42,.95),rgba(120,58,42,0) 70%),
    radial-gradient(ellipse 260px 380px at 1140px 80px,rgba(62,32,28,.95),rgba(62,32,28,0) 70%),
    radial-gradient(ellipse 420px 260px at 760px 560px,rgba(214,168,120,.8),rgba(214,168,120,0) 70%),
    linear-gradient(100deg,#57728f 0%,#9fb0ba 28%,#d3cdbb 50%,#c49774 68%,#8d4d37 85%,#5b2e24 100%)}
.brand-mark{left:171px;top:98px;display:flex;flex-direction:column;align-items:center;gap:10px;
  font-weight:700;font-size:34px;color:var(--white);text-shadow:0 2px 4px rgba(0,0,0,.3)}
.brand-mark .dot{width:56px;height:56px;border-radius:50%;background:var(--red)}
.nav{left:491px;top:56px;display:flex;gap:27px;font-size:15px;color:var(--white);letter-spacing:.2px}
.hero-text{left:171px;top:296px;color:var(--white);text-shadow:0 2px 4px rgba(0,0,0,.4);font-size:37px;line-height:52px}
.hero-text b{font-weight:700;text-transform:uppercase}

/* about */
.about-frame{left:123px;top:775px;width:430px;height:545px;background:var(--blue);transform:rotate(-3deg)}
.about-photo{left:143px;top:786px;width:381px;height:524px;box-shadow:0 4px 14px rgba(0,0,0,.25);
  background:
    radial-gradient(ellipse 120px 160px at 190px 250px,rgba(120,170,210,.9),rgba(120,170,210,0) 70%),
    radial-gradient(ellipse 110px 200px at 40px 230px,rgba(40,60,90,.8),rgba(40,60,90,0) 70%),
    radial-gradient(ellipse 110px 200px at 340px 230px,rgba(50,70,100,.8),rgba(50,70,100,0) 70%),
    radial-gradient(ellipse 130px 90px at 190px 430px,rgba(180,150,125,.9),rgba(180,150,125,0) 70%),
    linear-gradient(180deg,#3f4548 0%,#5f6d78 14%,#6f95b6 34%,#6d8aa0 52%,#7e6c5c 70%,#6a5a4d 86%,#4b4038 100%)}
.eyebrow{font-size:28px;color:var(--red);text-transform:uppercase;line-height:1}
.title{font-size:45px;font-weight:700;color:var(--blue);text-transform:uppercase;line-height:1}
.icon-dot{width:50px;height:50px;border-radius:50%;background:var(--red)}
.about-copy{left:599px;top:945px;width:430px;font-family:"Raleway",sans-serif;font-size:12.6px;line-height:26px;color:var(--muted);text-align:justify}
.about-copy p+p{margin-top:6px}
.btn{display:flex;align-items:center;justify-content:center;background:var(--blue);color:var(--white);font-size:15px;font-weight:700;text-transform:uppercase}

/* sections */
.cloud-band{background:
  radial-gradient(ellipse 420px 120px at 200px 700px,rgba(255,255,255,.95),rgba(255,255,255,0) 70%),
  radial-gradient(ellipse 500px 140px at 800px 740px,rgba(255,255,255,.9),rgba(255,255,255,0) 70%),
  radial-gradient(ellipse 400px 160px at 1050px 300px,rgba(255,255,255,.8),rgba(255,255,255,0) 70%),
  linear-gradient(180deg,#f4f6f8 0%,#e6ecf2 45%,#d8e0e9 80%,#e9eef3 100%)}
.tile{display:flex;align-items:flex-end;justify-content:center;padding-bottom:18px;color:var(--white);font-size:20px;text-transform:uppercase;box-shadow:0 3px 8px rgba(0,0,0,.2);text-shadow:0 1px 3px rgba(0,0,0,.5)}
.card{background:var(--white);box-shadow:0 2px 8px rgba(0,0,0,.12);display:flex;align-items:center;justify-content:center}
.tee{width:130px;height:110px}
.prod-label{text-align:center;width:187px}
.prod-name{font-size:21px;color:var(--ink)}
.prod-sub{font-size:12.5px;color:var(--ink);margin-top:6px}
.prod-price{font-size:22px;font-weight:700;color:var(--ink);margin-top:8px}
.prod-price.sale{color:var(--red)}
.insta{width:278px;height:199px}

/* contact */
.contact-brand{left:171px;top:3960px;width:232px;display:flex;flex-direction:column;align-items:center;gap:22px;font-size:42px;font-weight:700;color:var(--blue)}
.contact-brand .dot{width:150px;height:150px;border-radius:50%;background:var(--red)}
.field{border:1px solid var(--line);background:var(--white);font-size:15px;color:var(--ink);padding:18px 13px 0}
.footer-text{left:0;top:4455px;width:1200px;text-align:center;color:var(--white);font-size:15px;font-weight:700}
</style>
</head>
<body>

<!-- hero -->
<div class="abs hero" role="img" aria-label="Climber silhouetted on a cliff against a cloudy sunset sky"></div>
<svg class="abs" style="left:0;top:600px" width="1200" height="100" viewBox="0 0 1200 100" aria-hidden="true">
  <polygon points="600,38 1200,12 1200,83 940,83" fill="#0b4c9b"/>
  <polygon points="0,82 1200,46 1200,100 0,100" fill="#ffffff"/>
</svg>
<div class="abs brand-mark"><span class="dot"></span>TorbCutters</div>
<nav class="abs nav"><span>HOME</span><span>ABOUT</span><span>PRODUCT</span><span>TRAVEL ADVENTURE</span><span>BLOG</span><span>CONTACT</span></nav>
<div class="abs hero-text">
  <div>TorbCutters is a</div>
  <div><b>Livonia Barber Shop</b></div>
  <div>focused on providing</div>
  <div><b>High Quality Haircuts</b></div>
  <div>for men!</div>
</div>

<!-- about -->
<div class="abs about-frame"></div>
<div class="abs about-photo" role="img" aria-label="Interior of the barber shop with chairs, mirrors and a wooden front desk"></div>
<div class="abs icon-dot" style="left:599px;top:842px"></div>
<div class="abs eyebrow" style="left:676px;top:830px">About</div>
<div class="abs title" style="left:676px;top:868px">TorbCutters</div>
<div class="abs about-copy">
  <p>Nemo enim ipsam voluptatem quia voluptas sit aspernatur aut odit aut fugit, sed quia consequuntur magni dolores eos qui ratione voluptatem sequi nesciunt. Neque porro quisquam est, qui dolorem ipsum quia dolor sit amet, consectetur, adipisci velit, sed quia non numquam eius modi tempora incidunt ut labore et dolore magnam aliquam quaerat voluptatem.</p>
  <p>Neque porro quisquam est, qui dolorem ipsum quia dolor sit amet, consectetur, adipisci velit, sed quia non numquam eius modi tempora incidunt ut labore et dolore magnam aliquam quaerat voluptatem.</p>
</div>
<div class="abs btn" style="left:599px;top:1219px;width:118px;height:58px">Read More</div>

<!-- travel adventure -->
<div class="abs cloud-band" style="left:0;top:1460px;width:1200px;height:830px"></div>
<svg class="abs" style="left:0;top:1455px" width="1200" height="850" viewBox="0 0 1200 850" aria-hidden="true">
  <polygon points="0,4 600,42 0,82" fill="#0b4c9b"/>
  <polygon points="0,0 1200,0 1200,20 600,42 0,4" fill="#ffffff"/>
  <polygon points="1200,775 1200,835 720,810" fill="#0b4c9b"/>
  <polygon points="0,835 1200,835 1200,850 0,850" fill="#ffffff"/>
</svg>
<div class="abs icon-dot" style="left:171px;top:1610px"></div>
<div class="abs eyebrow" style="left:250px;top:1594px">My</div>
<div class="abs title" style="left:250px;top:1633px">Travel Adventure</div>
<svg class="abs" style="left:978px;top:1605px" width="50" height="56" viewBox="0 0 50 56" aria-hidden="true">
  <polyline points="18,2 4,28 18,54" fill="none" stroke="#555" stroke-width="2"/>
  <polyline points="32,2 46,28 32,54" fill="none" stroke="#555" stroke-width="2"/>
</svg>
<div class="abs tile" style="left:173px;top:1736px;width:299px;height:409px;background:
  linear-gradient(180deg,rgba(0,0,0,0) 70%,rgba(20,18,18,.75) 100%),
  radial-gradient(ellipse 160px 90px at 220px 250px,rgba(255,220,170,.95),rgba(255,220,170,0) 70%),
  radial-gradient(ellipse 120px 130px at 40px 270px,rgba(90,70,58,.9),rgba(90,70,58,0) 70%),
  linear-gradient(180deg,#cfc3b4 0%,#e2c9a6 35%,#d7a878 55%,#9d7a60 72%,#5d4a3f 100%)" role="img" aria-label="Traveller with raised arms on a beach at sunset">Dolorem eum fugiat</div>
<div class="abs tile" style="left:489px;top:1736px;width:260px;height:198px;background:
  linear-gradient(180deg,rgba(0,0,0,0) 60%,rgba(20,20,24,.7) 100%),
  radial-gradient(ellipse 110px 50px at 190px 80px,rgba(246,210,150,.9),rgba(246,210,150,0) 70%),
  radial-gradient(ellipse 140px 50px at 130px 130px,rgba(225,225,228,.85),rgba(225,225,228,0) 70%),
  linear-gradient(180deg,#6c86a3 0%,#a6b0b8 40%,#8d8a86 70%,#3d3c3e 100%)" role="img" aria-label="Hiker on a misty mountain peak">Dolorem eum fugiat</div>
<div class="abs tile" style="left:765px;top:1736px;width:260px;height:198px;background:
  linear-gradient(180deg,rgba(0,0,0,0) 60%,rgba(20,18,16,.7) 100%),
  radial-gradient(ellipse 90px 70px at 220px 60px,rgba(255,236,190,.95),rgba(255,236,190,0) 70%),
  radial-gradient(ellipse 200px 70px at 90px 160px,rgba(60,52,44,.9),rgba(60,52,44,0) 70%),
  linear-gradient(180deg,#b9b5a8 0%,#9d9380 45%,#6e6150 70%,#34302b 100%)" role="img" aria-label="Person with open arms on a mountain ridge">Dolorem eum fugiat</div>
<div class="abs tile" style="left:489px;top:1949px;width:260px;height:196px;background:
  linear-gradient(180deg,rgba(0,0,0,0) 60%,rgba(18,20,24,.7) 100%),
  radial-gradient(ellipse 150px 40px at 110px 80px,rgba(70,86,104,.9),rgba(70,86,104,0) 70%),
  linear-gradient(180deg,#4f6e95 0%,#8ea4bd 35%,#6b7b88 55%,#58606a 75%,#2d3136 100%)" role="img" aria-label="Motorcyclist facing a mountain range">Dolorem eum fugiat</div>
<div class="abs tile" style="left:765px;top:1949px;width:260px;height:196px;background:
  linear-gradient(180deg,rgba(0,0,0,0) 60%,rgba(20,16,16,.7) 100%),
  radial-gradient(ellipse 90px 40px at 110px 90px,rgba(255,214,130,.95),rgba(255,214,130,0) 70%),
  linear-gradient(180deg,#4c5a78 0%,#b07d67 30%,#e49b55 48%,#a85e35 62%,#3a2b27 80%,#221c1c 100%)" role="img" aria-label="Person sitting on a cliff watching the sunset over the sea">Dolorem eum fugiat</div>

<!-- featured products -->
<svg class="abs" style="left:173px;top:2410px" width="50" height="56" viewBox="0 0 50 56" aria-hidden="true">
  <polyline points="18,2 4,28 18,54" fill="none" stroke="#555" stroke-width="2"/>
  <polyline points="32,2 46,28 32,54" fill="none" stroke="#555" stroke-width="2"/>
</svg>
<div class="abs eyebrow" style="left:700px;top:2398px;width:252px;text-align:right">My</div>
<div class="abs title" style="left:500px;top:2437px;width:452px;text-align:right">Featured Products</div>
<div class="abs icon-dot" style="left:970px;top:2412px"></div>

<div class="abs card" style="left:173px;top:2550px;width:187px;height:227px"><svg class="tee" viewBox="0 0 130 110" role="img" aria-label="White T-shirt"><path d="M40 5 L20 15 L4 38 L22 48 L30 38 L30 105 L100 105 L100 38 L108 48 L126 38 L110 15 L90 5 Q65 22 40 5Z" fill="#f3f3f3" stroke="#d6d6d6"/></svg></div>
<div class="abs card" style="left:395px;top:2550px;width:187px;height:227px"><svg class="tee" viewBox="0 0 130 110" role="img" aria-label="Charcoal T-shirt"><path d="M40 5 L20 15 L4 38 L22 48 L30 38 L30 105 L100 105 L100 38 L108 48 L126 38 L110 15 L90 5 Q65 22 40 5Z" fill="#575757"/></svg></div>
<div class="abs card" style="left:617px;top:2550px;width:186px;height:227px"><svg class="tee" viewBox="0 0 130 110" role="img" aria-label="Grey T-shirt"><path d="M40 5 L20 15 L4 38 L22 48 L30 38 L30 105 L100 105 L100 38 L108 48 L126 38 L110 15 L90 5 Q65 22 40 5Z" fill="#a3a3a3"/></svg></div>
<div class="abs card" style="left:838px;top:2550px;width:187px;height:227px"><svg class="tee" viewBox="0 0 130 110" role="img" aria-label="Green T-shirt"><path d="M40 5 L20 15 L4 38 L22 48 L30 38 L30 105 L100 105 L100 38 L108 48 L126 38 L110 15 L90 5 Q65 22 40 5Z" fill="#129a2f"/></svg></div>

<div class="abs prod-label" style="left:173px;top:2804px"><div class="prod-name">T-SHIRTS</div><div class="prod-sub">SED UT PERSPICIATIS</div><div class="prod-price sale">$30.00</div></div>
<div class="abs prod-label" style="left:395px;top:2804px"><div class="prod-name">T-SHIRTS</div><div class="prod-sub">SED UT PERSPICIATIS</div><div class="prod-price">$30.00</div></div>
<div class="abs prod-label" style="left:617px;top:2804px"><div class="prod-name">T-SHIRTS</div><div class="prod-sub">SED UT PERSPICIATIS</div><div class="prod-price">$30.00</div></div>
<div class="abs prod-label" style="left:838px;top:2804px"><div class="prod-name">T-SHIRTS</div><div class="prod-sub">SED UT PERSPICIATIS</div><div class="prod-price">$30.00</div></div>

<!-- instagram -->
<div class="abs cloud-band" style="left:0;top:2970px;width:1200px;height:835px"></div>
<svg class="abs" style="left:0;top:2965px" width="1200" height="850" viewBox="0 0 1200 850" aria-hidden="true">
  <polygon points="0,4 600,42 0,82" fill="#0b4c9b"/>
  <polygon points="0,0 1200,0 1200,20 600,42 0,4" fill="#ffffff"/>
  <polygon points="1200,772 1200,838 720,810" fill="#0b4c9b"/>
  <polygon points="0,838 1200,838 1200,850 0,850" fill="#ffffff"/>
</svg>
<div class="abs icon-dot" style="left:171px;top:3120px"></div>
<div class="abs eyebrow" style="left:250px;top:3104px">Instagram</div>
<div class="abs title" style="left:250px;top:3143px">@torbcuttersformen</div>
<svg class="abs" style="left:978px;top:3115px" width="50" height="56" viewBox="0 0 50 56" aria-hidden="true">
  <polyline points="18,2 4,28 18,54" fill="none" stroke="#555" stroke-width="2"/>
  <polyline points="32,2 46,28 32,54" fill="none" stroke="#555" stroke-width="2"/>
</svg>
<div class="abs insta" style="left:171px;top:3245px;background:
  radial-gradient(ellipse 50px 70px at 170px 110px,rgba(210,225,235,.95),rgba(210,225,235,0) 70%),
  radial-gradient(ellipse 70px 120px at 60px 100px,rgba(28,52,100,.9),rgba(28,52,100,0) 70%),
  linear-gradient(90deg,#1f3e74 0%,#4e6786 30%,#8b8378 55%,#b9b1a5 70%,#2f6aa6 88%,#1d3d66 100%)" role="img" aria-label="Shop hallway with a sliding barn door"></div>
<div class="abs insta" style="left:461px;top:3245px;background:
  radial-gradient(ellipse 90px 70px at 200px 80px,rgba(255,224,160,.95),rgba(255,224,160,0) 70%),
  radial-gradient(ellipse 80px 100px at 70px 120px,rgba(60,48,42,.9),rgba(60,48,42,0) 70%),
  linear-gradient(90deg,#2e2622 0%,#6b5242 35%,#c48c55 65%,#e8be82 100%)" role="img" aria-label="Traveller looking out of a van window with a motivational slogan"></div>
<div class="abs insta" style="left:749px;top:3245px;background:
  radial-gradient(ellipse 120px 40px at 140px 70px,rgba(240,222,190,.9),rgba(240,222,190,0) 70%),
  radial-gradient(ellipse 90px 50px at 140px 180px,rgba(120,100,80,.9),rgba(120,100,80,0) 70%),
  linear-gradient(180deg,#b7a284 0%,#d8c6a4 30%,#8b8a6a 55%,#4f5c3c 78%,#2f3a26 100%)" role="img" aria-label="Hiker standing on a rock above misty hills"></div>
<div class="abs insta" style="left:171px;top:3458px;background:
  radial-gradient(ellipse 70px 60px at 50px 160px,rgba(70,66,62,.9),rgba(70,66,62,0) 70%),
  radial-gradient(ellipse 160px 40px at 180px 120px,rgba(160,185,210,.9),rgba(160,185,210,0) 70%),
  linear-gradient(180deg,#dfe8f0 0%,#bccfe0 35%,#8ea8c4 60%,#6e88a6 80%,#55677c 100%)" role="img" aria-label="Backpacker on a summit facing blue mountains"></div>
<div class="abs insta" style="left:461px;top:3458px;background:
  radial-gradient(ellipse 50px 110px at 140px 80px,rgba(255,196,120,.95),rgba(255,196,120,0) 70%),
  radial-gradient(ellipse 80px 130px at 20px 100px,rgba(70,24,14,.95),rgba(70,24,14,0) 70%),
  radial-gradient(ellipse 80px 130px at 260px 100px,rgba(80,28,16,.95),rgba(80,28,16,0) 70%),
  linear-gradient(180deg,#7a2c18 0%,#b84e26 45%,#8a3a1e 75%,#3a1a12 100%)" role="img" aria-label="Person walking through a red canyon"></div>
<div class="abs insta" style="left:749px;top:3458px;background:
  radial-gradient(ellipse 140px 60px at 90px 110px,rgba(235,232,226,.95),rgba(235,232,226,0) 70%),
  radial-gradient(ellipse 80px 110px at 240px 130px,rgba(120,80,50,.95),rgba(120,80,50,0) 70%),
  linear-gradient(90deg,#8f979e 0%,#bfbab1 45%,#d9b48a 70%,#7a5a40 100%)" role="img" aria-label="Climber helping another up a rock above the clouds"></div>

<!-- contact -->
<div class="abs contact-brand"><span class="dot"></span>TorbCutters</div>
<div class="abs eyebrow" style="left:463px;top:3907px">Form</div>
<div class="abs title" style="left:463px;top:3947px">Contact Us</div>
<div class="abs field" style="left:465px;top:4021px;width:277px;height:58px">First Name</div>
<div class="abs field" style="left:749px;top:4021px;width:277px;height:58px">Last Name</div>
<div class="abs field" style="left:465px;top:4089px;width:277px;height:58px">Email</div>
<div class="abs field" style="left:749px;top:4089px;width:277px;height:58px">Phone</div>
<div class="abs field" style="left:465px;top:4157px;width:561px;height:92px">Message</div>
<div class="abs btn" style="left:465px;top:4262px;width:126px;height:58px">Submit Here</div>

<!-- footer -->
<svg class="abs" style="left:0;top:4380px" width="1200" height="118" viewBox="0 0 1200 118" aria-hidden="true">
  <polygon points="0,38 1200,4 1200,118 0,118" fill="#0b4c9b"/>
</svg>
<div class="abs footer-text">COPYRIGHTS @ 2021 TORBCUTTERS.</div>

</body>
</html>
```